Wine Bottle Label for Corra Winslow California Wine

This will be a wine bottle label. The wine is produced from grapes from our family farm. Images at bottom are some of same ones in high resolution

Corra Winslow
Reserve Pinot Noir
Clarksburg 2023
Estate Grown (in cursive)

We would like to have a view from above, looking down from the levee there is a slough (wing of a river) running behind it, it looks down over vineyards, a big wood barn, a giant Oak Tree beyond the barn. There are beautiful sunsets there in the distance. Many birds fly over the vineyards including small black birds (as shown in one photo). Please use what you can from these suggestions to make a label. We will need a small image for back label and wording on it.

Other font styles liked:
• Wine bottle fonts

Requirements
Must have
• Wording mentioned . An Oak Tree with images of the vines and a sunset
Nice to have
• Flock of black birds flying in the sky

```html
<!DOCTYPE html>
<html lang="en">
<head>
<meta charset="utf-8">
<title>Corra Winslow Reserve Pinot Noir – Front Label</title>
<link rel="stylesheet" href="https://fonts.googleapis.com/css2?family=Cinzel:wght@500;700&family=Cormorant+Garamond:wght@500;600&family=Pinyon+Script&display=swap">
<style>
  :root {
    --backdrop: #1d1c1c;
    --label-cream: #f1ead8;
    --label-edge: #e3d9c1;
    --ink: #2b2725;
    --ink-soft: #4a4440;
    --script-red: #c0202a;
    --sketch-light: #e6e0d2;
    --sketch-dark: #9a958c;
  }
  * { margin: 0; padding: 0; box-sizing: border-box; }
  html, body {
    width: 1200px;
    height: 900px;
    overflow: hidden;
    background: var(--backdrop);
  }
  .front-label {
    position: absolute;
    left: 333px;
    top: 35px;
    width: 534px;
    height: 830px;
    color: var(--ink);
    text-align: center;
  }
  .label-shape {
    position: absolute;
    inset: 0;
    width: 100%;
    height: 100%;
  }
  .brand-name {
    position: absolute;
    top: 160px;
    left: 0;
    right: 0;
    font-family: "Cinzel", serif;
    font-weight: 500;
    font-size: 46px;
    letter-spacing: 1px;
    color: var(--ink);
  }
  .vineyard-scene {
    position: absolute;
    top: 268px;
    left: 28px;
    width: 478px;
    height: 286px;
    background: linear-gradient(180deg, var(--label-cream) 0%, var(--sketch-light) 35%, var(--sketch-dark) 100%);
    border-radius: 2px;
  }
  .wine-name {
    position: absolute;
    top: 580px;
    left: 0;
    right: 0;
    font-family: "Cinzel", serif;
    font-weight: 700;
    font-size: 37px;
    color: var(--ink);
  }
  .vintage {
    position: absolute;
    top: 635px;
    left: 0;
    right: 0;
    font-family: "Cormorant Garamond", serif;
    font-weight: 600;
    font-size: 26px;
    color: var(--ink);
  }
  .appellation {
    position: absolute;
    top: 683px;
    left: 0;
    right: 0;
    font-family: "Cinzel", serif;
    font-weight: 500;
    font-size: 24px;
    letter-spacing: 1px;
    color: var(--ink-soft);
  }
  .estate-grown {
    position: absolute;
    top: 712px;
    left: 0;
    right: 0;
    font-family: "Pinyon Script", cursive;
    font-size: 40px;
    color: var(--script-red);
  }
  .label-footer {
    position: absolute;
    left: 30px;
    right: 30px;
    bottom: 20px;
    display: flex;
    justify-content: space-between;
    font-family: "Cormorant Garamond", serif;
    font-weight: 600;
    font-size: 18px;
    color: var(--ink);
  }
</style>
</head>
<body>
  <section class="front-label">
    <svg class="label-shape" viewBox="0 0 534 830" preserveAspectRatio="none" aria-hidden="true">
      <path d="M0,105 Q220,15 534,0 L534,830 L0,830 Z" fill="var(--label-cream)"/>
      <path d="M0,105 Q220,15 534,0 L534,22 Q230,38 0,128 Z" fill="var(--label-edge)"/>
    </svg>

    <h1 class="brand-name">Corra Winslow</h1>

    <div class="vineyard-scene" role="img" aria-label="Pen sketch of vineyard rows stretching toward trees on the horizon"></div>

    <h2 class="wine-name">Reserve Pinot Noir</h2>
    <p class="vintage">2023</p>
    <p class="appellation">Clarksburg</p>
    <p class="estate-grown">Estate Grown</p>

    <div class="label-footer">
      <span class="volume">750ML</span>
      <span class="alcohol">ALC. 14.0% VOL</span>
    </div>
  </section>
</body>
</html>
```